Webdesign für neue Weinmarke
Zielgruppe
Kelchwandler ist eine neue Weinmarke. Es wird vorerst drei grundlegende Sorten geben: einen Rotwein, einen Weißwein und einen Rosé. Für diese neue Weinmarke wollen wir eine Webseite gestalten, welche die Weine ansprechend darstellt und zusätzlich den Kunden die Möglichkeit gibt, mehr Informationen über den Wein einzuholen. Die Marke Kelchwandler ist auch im Etikett an den Graf von Tressenbach angelehnt. Das Etikett zeigt den Baron, wie er auf einem Weinfass reitet – daher der Name „Kelchwandler“. Die Story, die wir mit dem Wein spielen, ist, dass die besonderen Fähigkeiten des Barons auch auf den Genuss des Kelchwandler zurückzuführen sind.
Die Zielgruppe für den Kelchwandler ist breit gefächert und schließt per se erst mal keine Personengruppe aus. Der Wein soll eher im niedrigeren Preissegment verkauft werden.
Aufgabenstellung
Es soll eine neue Webseite designt werden, die sich im Aufbau an der die Webseite http://www.velgor-example.de/#!/de/unsere-weine/sortiment orientieren kann. Zudem können für die Entwicklung kleine Animationen berücksichtigt werden, die die Seite auflockern. Das Design soll eine responsive Webseite unterstützen. Das Design soll zur Weinmarke Kelchwandler passen von der wir bisher nur das Etikett haben.

```html
<!DOCTYPE html>
<html lang="de">
<head>
<meta charset="utf-8">
<title>Kelchwandler – Webdesign</title>
<link rel="stylesheet" href="https://fonts.googleapis.com/css2?family=Open+Sans:wght@400;600;700&family=PT+Sans+Narrow:wght@400;700&display=swap">
<style>
  :root {
    --page-bg: #fdfcf5;
    --screen-bg: #f5f3ec;
    --ink: #2b2a28;
    --nav-ink: #55534e;
    --vineyard-light: #f1efe6;
    --vineyard-mid: #e2e0d5;
    --figure-tone: #8d8b85;
    --white: #ffffff;

    --rose-band: #dc585a;
    --rose-bar: #a94547;
    --riesling-band: #a5c24a;
    --riesling-bar: #7e9340;
    --red-band: #8b3425;
    --red-bar: #6d291d;

    --bottle-red: #2a1a1e;
    --bottle-rose: #d8384a;
    --bottle-white: #b6b046;
  }
  * { box-sizing: border-box; margin: 0; padding: 0; }
  html, body { width: 675px; height: 1200px; overflow: hidden; background: var(--page-bg); }
  body { position: relative; font-family: "Open Sans", sans-serif; }

  .screen {
    position: absolute;
    left: 134px;
    width: 406px;
    height: 254px;
    background: var(--screen-bg);
    overflow: hidden;
  }
  .screen--rose { top: 71px; --band: var(--rose-band); --bar: var(--rose-bar); }
  .screen--riesling { top: 446px; --band: var(--riesling-band); --bar: var(--riesling-bar); }
  .screen--red { top: 821px; --band: var(--red-band); --bar: var(--red-bar); }

  .site-header { position: absolute; left: 47px; right: 46px; top: 12px; height: 10px; }
  .brand {
    position: absolute; left: 0; top: 0;
    font-family: "Open Sans", sans-serif; font-weight: 700;
    font-size: 8px; letter-spacing: 0.2px; color: var(--ink); line-height: 10px;
  }
  .main-nav {
    position: absolute; right: 0; top: 3px;
    display: flex; gap: 5.5px;
    font-size: 4.2px; line-height: 5px; letter-spacing: 0.15px;
    color: var(--nav-ink); text-transform: uppercase;
  }
  .main-nav .is-active { color: var(--ink); font-weight: 700; }

  .hero-vineyard {
    position: absolute; left: 0; top: 40px; width: 406px; height: 118px;
    background: linear-gradient(180deg, var(--vineyard-light) 0%, var(--vineyard-mid) 55%, var(--vineyard-light) 100%);
  }
  .hero-figure {
    position: absolute; left: 82px; top: 34px; width: 128px; height: 124px;
    background: radial-gradient(ellipse at 45% 50%, #6f6d68 0%, var(--figure-tone) 60%, #c9c7be 100%);
    border-radius: 46% 46% 6px 6px;
  }

  .hero-band {
    position: absolute; left: 0; top: 158px; width: 406px; height: 76px;
    background: var(--band);
  }
  .hero-title {
    position: absolute; left: 47px; top: 170px; z-index: 2;
    white-space: nowrap;
    font-family: "PT Sans Narrow", sans-serif; font-weight: 700;
    font-size: 10.4px; line-height: 9.8px; color: var(--white); text-transform: uppercase;
  }
  .hero-copy {
    position: absolute; left: 47px; top: 195.5px; width: 162px; z-index: 2;
    font-size: 3.9px; line-height: 6.2px; color: var(--white); opacity: 0.92;
  }
  .hero-cta {
    position: absolute; left: 47px; top: 218px; z-index: 2;
    display: flex; align-items: center; gap: 4px;
    font-family: "PT Sans Narrow", sans-serif; font-weight: 700;
    font-size: 4.8px; line-height: 6px; color: var(--white); text-transform: uppercase;
  }
  .hero-cta svg { width: 7px; height: 5px; }

  .bottle { position: absolute; border-radius: 3px 3px 2px 2px; }
  .bottle--red { background: linear-gradient(90deg, #1a1013, var(--bottle-red) 45%, #120a0c); }
  .bottle--rose { background: linear-gradient(90deg, #b52436, var(--bottle-rose) 45%, #a81f30); }
  .bottle--white { background: linear-gradient(90deg, #8f8a2c, var(--bottle-white) 45%, #86812a); }
  .pos-left { left: 234px; top: 64px; width: 32px; height: 152px; }
  .pos-center { left: 267px; top: 49px; width: 35px; height: 171px; }
  .pos-right { left: 302px; top: 63px; width: 31px; height: 153px; }

  .product-tabs {
    position: absolute; left: 0; top: 234px; width: 406px; height: 20px;
    background: var(--bar);
  }
  .product-tabs::before {
    content: ""; position: absolute; left: 199.5px; top: -3.5px;
    border-left: 4px solid transparent; border-right: 4px solid transparent;
    border-bottom: 3.5px solid var(--bar);
  }
  .product-tab {
    position: absolute; top: 7px; transform: translateX(-50%); white-space: nowrap;
    font-family: "PT Sans Narrow", sans-serif; font-weight: 700;
    font-size: 5px; line-height: 6px; color: rgba(255,255,255,0.6); text-transform: uppercase;
  }
  .product-tab--left { left: 96px; }
  .product-tab--center { left: 203px; color: var(--white); }
  .product-tab--right { left: 310px; }
</style>
</head>
<body>

<section class="screen screen--rose">
  <header class="site-header">
    <div class="brand">KELCHWANDLER</div>
    <nav class="main-nav"><span class="is-active">Home</span><span>Rotwein</span><span>Rosé</span><span>Weißwein</span><span>Regionen</span><span>Der Baron</span></nav>
  </header>
  <div class="hero-vineyard" role="img" aria-label="Gezeichnete Weinberglandschaft"></div>
  <div class="hero-figure" role="img" aria-label="Kupferstich-Illustration des Barons mit Weinglas auf einem Fass"></div>
  <div class="hero-band"></div>
  <h1 class="hero-title">Der Wein, der schon dem Baron<br>selbst Anmut &amp; Heldengeist verlieh</h1>
  <p class="hero-copy">Genießen Sie Kelchwandler als gehaltvollen und fruchtbetonten Rotwein, als lieblichen und fruchtigen Rosé oder als feinherben Riesling. Die drei Weine überzeugen durch höchste Qualität, harmonische Säuren und ein außergewöhnliches Design.</p>
  <a class="hero-cta">Zu den Produkten <svg viewBox="0 0 7 5"><path d="M0 2.5h6M4 .5l2 2-2 2" fill="none" stroke="#fff" stroke-width=".6"/></svg></a>
  <div class="bottle bottle--red pos-left" role="img" aria-label="Flaschenfoto Dornfelder halbtrocken"></div>
  <div class="bottle bottle--rose pos-center" role="img" aria-label="Flaschenfoto Dornfelder Rosé"></div>
  <div class="bottle bottle--white pos-right" role="img" aria-label="Flaschenfoto Riesling feinherb"></div>
  <nav class="product-tabs">
    <span class="product-tab product-tab--left">Dornfelder halbtrocken</span>
    <span class="product-tab product-tab--center">Dornfelder Rosé</span>
    <span class="product-tab product-tab--right">Riesling feinherb</span>
  </nav>
</section>

<section class="screen screen--riesling">
  <header class="site-header">
    <div class="brand">KELCHWANDLER</div>
    <nav class="main-nav"><span class="is-active">Home</span><span>Rotwein</span><span>Rosé</span><span>Weißwein</span><span>Regionen</span><span>Der Baron</span></nav>
  </header>
  <div class="hero-vineyard" role="img" aria-label="Gezeichnete Weinberglandschaft"></div>
  <div class="hero-figure" role="img" aria-label="Kupferstich-Illustration des Barons mit Weinglas auf einem Fass"></div>
  <div class="hero-band"></div>
  <h1 class="hero-title">Der Wein, der schon dem Baron<br>selbst Anmut &amp; Heldengeist verlieh</h1>
  <p class="hero-copy">Genießen Sie Kelchwandler als gehaltvollen und fruchtbetonten Rotwein, als lieblichen und fruchtigen Rosé oder als feinherben Riesling. Die drei Weine überzeugen durch höchste Qualität, harmonische Säuren und ein außergewöhnliches Design.</p>
  <a class="hero-cta">Zu den Produkten <svg viewBox="0 0 7 5"><path d="M0 2.5h6M4 .5l2 2-2 2" fill="none" stroke="#fff" stroke-width=".6"/></svg></a>
  <div class="bottle bottle--red pos-left" role="img" aria-label="Flaschenfoto Dornfelder halbtrocken"></div>
  <div class="bottle bottle--white pos-center" role="img" aria-label="Flaschenfoto Riesling feinherb"></div>
  <div class="bottle bottle--rose pos-right" role="img" aria-label="Flaschenfoto Dornfelder Rosé"></div>
  <nav class="product-tabs">
    <span class="product-tab product-tab--left">Dornfelder halbtrocken</span>
    <span class="product-tab product-tab--center">Riesling feinherb</span>
    <span class="product-tab product-tab--right">Dornfelder Rosé</span>
  </nav>
</section>

<section class="screen screen--red">
  <header class="site-header">
    <div class="brand">KELCHWANDLER</div>
    <nav class="main-nav"><span class="is-active">Home</span><span>Rotwein</span><span>Rosé</span><span>Weißwein</span><span>Regionen</span><span>Der Baron</span></nav>
  </header>
  <div class="hero-vineyard" role="img" aria-label="Gezeichnete Weinberglandschaft"></div>
  <div class="hero-figure" role="img" aria-label="Kupferstich-Illustration des Barons mit Weinglas auf einem Fass"></div>
  <div class="hero-band"></div>
  <h1 class="hero-title">Der Wein, der schon dem Baron<br>selbst Anmut &amp; Heldengeist verlieh</h1>
  <p class="hero-copy">Genießen Sie Kelchwandler als gehaltvollen und fruchtbetonten Rotwein, als lieblichen und fruchtigen Rosé oder als feinherben Riesling. Die drei Weine überzeugen durch höchste Qualität, harmonische Säuren und ein außergewöhnliches Design.</p>
  <a class="hero-cta">Zu den Produkten <svg viewBox="0 0 7 5"><path d="M0 2.5h6M4 .5l2 2-2 2" fill="none" stroke="#fff" stroke-width=".6"/></svg></a>
  <div class="bottle bottle--white pos-left" role="img" aria-label="Flaschenfoto Riesling feinherb"></div>
  <div class="bottle bottle--red pos-center" role="img" aria-label="Flaschenfoto Dornfelder halbtrocken"></div>
  <div class="bottle bottle--rose pos-right" role="img" aria-label="Flaschenfoto Dornfelder Rosé"></div>
  <nav class="product-tabs">
    <span class="product-tab product-tab--left">Dornfelder Rosé</span>
    <span class="product-tab product-tab--center">Dornfelder halbtrocken</span>
    <span class="product-tab product-tab--right">Riesling feinherb</span>
  </nav>
</section>

</body>
</html>
```